E-Commerce Web Design Project - Online Designer Childrens Clothing

I currently have a website at http://qrk.example/Tm4vRa but I am not happy with the look and feel. I mainly want black and white colours as my images will have splashes of colour

I am going for a complete new look and will require the following:

1. Home page - to have categories listed on the left side bar and large scrolling images in the center (600px by 450px) with 3 static boxes equally spaced underneath (325px by 142px) so that I can change them to different links. 3 static boxes to be on the right side bar in vertical position each size (198px by 145px).

2. category pages - to have image across the width of the page for my category title page eg. Marbury's kids. category pages to have 3 products across and ability to view all or go down to the page fold.

3. product Details pages - product image to be on the left side bar. All drop down boxes to be of equal size in width and length. Other products you may like is to be removed. Please see the following links as to what I would like it to look like layout wise http://qrk.example/Wp7dGs

4. All other pages such as the Contact us, T's and C's, About Us, Ordering and Delivery etc to have the same template where I will be able to keep adding pages as I need to.

I will be transferring my services to Tillvane and will seek a web developer once the design is confirmed.

3 websites that i love are the following:
http://qrk.example/Wp7dGs
http://qrk.example/Bz2fUe
http://qrk.example/3JtYon
http://qrk.example/gumaLQ

I want my website to be sleek and modern and have a fashion magazine feel to it. the layout is to be clean with everything in proportion. I already have my logo in greyscale that I have attached it to this project.

Please let me know if you have further questions.
Updates

would love to see more designs!i have added a couple more logo files also to add.

Reason: I have now guaranteed tthis project so hopefully more designs will come through!!

I have now guranteed this project so would love to see a few more designs!!!

Reason: I need time to review all submissions and request changes if need be

Target Market(s)

women 25-45 on good disposable income who like their designer brands and love to dress their boys in them

Industry/Entity Type

Fashion

Requirements
Must have
• must be easy to navigate and not to busy. nice and sleek with a fashion magazine feel to it. want it to be more monotone in black and white as my images will add colour
Nice to have
• I love the look of the following websites.

Home Pages:
http://qrk.example/3JtYon
http://qrk.example/Bz2fUe
http://qrk.example/hRN8T4
http://qrk.example/wiDk2v
http://qrk.example/Ezm5o
http://qrk.example/xTcHoa
http://qrk.example/P3sRyd

Category Page:

Product Details Page:
http://qrk.example/Wp7dGs
http://qrk.example/NuqaWt
http://qrk.example/RfzvIm

Products details page:
http://qrk.example/G6WJ9k
http://qrk.example/Wp7dGs

Should not have
• I do not want any quirky or childlike illustrations or the colorful blue. this website is for boys clothing but it targeted at women!!

```html
<!DOCTYPE html>
<html lang="en">
<head>
<meta charset="utf-8">
<title>Dapper Lads Clothing</title>
<link href="https://fonts.googleapis.com/css2?family=Questrial&family=Poiret+One&family=Abel&display=swap" rel="stylesheet">
<style>
:root{
  --ink:#333;
  --muted:#666;
  --orange:#f28a00;
  --red:#d40000;
  --frame:#e3e3e3;
  --nav-top:#5a5a5a;
  --nav-bot:#1c1c1c;
  --dark:#2e2e2e;
  --white:#fff;
}
*{margin:0;padding:0;box-sizing:border-box}
html,body{width:898px;height:1200px;overflow:hidden;background:var(--white)}
body{font-family:"Questrial",sans-serif;color:var(--ink);position:relative}
.abs{position:absolute}
/* header */
.brand{left:36px;top:18px;width:170px;height:106px;border:2px solid #ddd;border-radius:6px;background:var(--white);display:flex;flex-direction:column;justify-content:center;align-items:center}
.brand-name{font-size:24px;line-height:28px;color:#222;text-align:center}
.brand-tag{font-size:8.5px;color:var(--orange);margin-top:6px;letter-spacing:.5px}
.header-photo{left:206px;top:8px;width:176px;height:126px;border-radius:40% 30% 20% 45%;background:linear-gradient(100deg,#fff 0%,#e9d6c6 22%,#cfb29a 45%,#9fb3c8 70%,#e8eef4 88%,#fff 100%)}
.top-links{right:26px;top:13px;font-size:11px;color:var(--muted)}
.top-links .hl{color:var(--orange)}
.account-bar{right:26px;top:51px;font-size:12px;color:#444;display:flex;gap:14px;align-items:center}
.account-bar .ico{display:inline-block;width:9px;height:9px;border:1.5px solid var(--orange);margin-right:5px;vertical-align:-1px}
.bag-count{display:inline-block;background:var(--orange);color:#fff;font-size:8px;padding:3px 4px;border-radius:2px;margin-left:2px}
.total b{color:var(--orange);font-weight:normal}
.search{left:648px;top:85px;width:224px;height:23px;border:1px solid #ccc;display:flex}
.search .field{flex:1;background:#fff}
.search .btn{width:63px;background:#e2e2e2;font-size:10px;color:#555;display:flex;align-items:center;justify-content:center}
.delivery-note{right:26px;top:119px;font-size:10px;color:var(--muted)}
.main-nav{left:25px;top:140px;width:847px;height:26px;background:linear-gradient(var(--nav-top),var(--nav-bot));display:flex;justify-content:space-around;align-items:center}
.main-nav a{color:#fff;font-size:12px;text-decoration:none}
/* sidebar */
.shop-title{left:25px;top:172px;width:158px;font-size:15px;color:var(--orange);border-bottom:3px solid #ddd;padding-bottom:3px}
.shop-list{left:28px;top:201px;list-style:none;font-size:12px;color:#444}
.shop-list li{height:20.3px;display:flex;align-items:center;gap:7px}
.shop-list li::before{content:"";width:4px;height:9px;background:var(--orange);border-radius:2px}
.sale-box{left:25px;top:453px;width:158px;height:100px}
.sale-word{left:0;top:0;font-size:34px;color:var(--orange);line-height:34px}
.sale-panel{left:0;top:32px;width:158px;height:68px;background:linear-gradient(#ffa300,#f07d00);border-bottom:4px solid #ffe36a}
.sale-panel span{position:absolute;color:#fff;font-size:21px;line-height:22px;left:36px;top:7px}
.sale-panel span.by{left:62px;top:28px}
/* banners */
.frame{background:var(--frame)}
.fill{position:absolute;left:5px;top:5px;right:5px;bottom:5px;overflow:hidden}
.hero{left:190px;top:174px;width:508px;height:379px}
.hero-img{background:
  linear-gradient(90deg,rgba(40,40,40,.0) 0%,rgba(40,40,40,0) 45%,rgba(110,110,110,.95) 62%,#8a8a8a 100%),
  linear-gradient(180deg,#b7c4cc 0%,#a8b6bf 18%,#d9bba2 32%,#c9a189 48%,#7a5e50 66%,#5a6470 82%,#3e4650 100%),
  #555}
.hero-title{left:278px;top:18px;font-family:"Poiret One",sans-serif;font-variant:small-caps;font-size:34px;line-height:32px;color:#f2f2f2}
.hero-title span{display:block;padding-left:86px}
.save{left:265px;top:104px;display:flex;align-items:flex-end;color:#fff}
.save .v{writing-mode:vertical-rl;transform:rotate(180deg);font-size:22px;color:#1a1a1a;margin-right:4px;margin-bottom:4px}
.save .big{font-size:78px;line-height:70px}
.save .upto{position:absolute;left:86px;top:14px;font-size:19px;line-height:19px;color:#333;text-align:center;background:rgba(255,255,255,.15)}
.save .on{font-size:25px;color:#111;margin-left:3px;margin-bottom:2px}
.hero-items{left:352px;top:222px;font-family:"Poiret One",sans-serif;font-size:21px;color:#fff;list-style:none;line-height:28px}
.hero-items li::before{content:"";display:inline-block;width:5px;height:12px;border-radius:3px;background:#222;margin-right:8px;vertical-align:-1px}
.shop-now{background:var(--dark);color:#fff;font-size:12px;padding:4px 0;width:82px;text-align:center}
.side-box{left:705px;width:167px;height:121px}
.gift-text{left:10px;top:0;bottom:0;display:flex;flex-direction:column;justify-content:center;font-family:"Poiret One",sans-serif;color:#888}
/* promo row */
.promo{top:561px;height:119px}
.promo .shop-now{position:absolute;right:0;bottom:0}
.fs-title{font-family:"Poiret One",sans-serif;font-size:30px;color:#222;left:10px;top:8px}
.fs-sub{font-family:"Poiret One",sans-serif;font-size:16px;color:#222;left:34px;top:47px}
.fs-price{left:30px;top:68px;display:flex;align-items:baseline;gap:6px}
.fs-price b{font-family:"Poiret One",sans-serif;font-weight:normal;font-size:38px;color:var(--orange)}
.fs-price small{font-size:11px;color:#222}
.nl-big{left:8px;top:4px;font-size:38px;color:var(--orange)}
.nl-receive{left:84px;top:8px;font-size:13px;color:#222;line-height:14px}
.nl-receive b{font-size:24px;font-weight:normal;display:block;line-height:22px}
.nl-copy{left:148px;top:10px;font-size:11.5px;color:#333;line-height:16px}
.nl-word{left:4px;top:46px;font-family:"Poiret One",sans-serif;font-size:39px;color:#ddd}
.nl-email{left:0;bottom:0;width:228px;height:20px;background:var(--dark);color:#bbb;font-size:11px;padding:3px 7px}
.nl-ok{right:0;bottom:0;width:33px;height:20px;background:var(--orange);color:#fff;font-size:15px;text-align:center;line-height:20px}
/* featured */
.feat-tab{left:25px;top:695px;width:200px;height:30px;background:#ddd;clip-path:polygon(0 0,88% 0,100% 100%,0 100%);font-size:16px;color:#555;padding:6px 15px}
.feat-box{left:25px;top:723px;width:847px;height:224px;border:5px solid #ddd;background:var(--white)}
.arrow{top:64px;width:14px;height:70px;background:#ccc}
.arrow.l{left:14px;clip-path:polygon(100% 0,0 50%,100% 100%)}
.arrow.r{right:14px;clip-path:polygon(0 0,100% 50%,0 100%)}
.card{top:16px;width:125px;height:188px;background:#eee;border-bottom:2px solid #ccc}
.card .pic{position:absolute;left:6px;top:6px;width:113px;height:128px;background:#fff}
.card .pic i{position:absolute;left:14px;top:16px;right:14px;bottom:16px;border-radius:10px}
.card .name{position:absolute;top:146px;width:100%;text-align:center;font-family:"Abel",sans-serif;font-size:10px;color:#333}
.card .price{position:absolute;top:158px;width:100%;text-align:center;font-size:10px;color:var(--red)}
.card .rrp{position:absolute;top:170px;width:100%;text-align:center;font-size:10px;color:#555;text-decoration:line-through}
/* footer */
.foot-head{left:25px;top:956px;width:847px;height:27px;background:#ddd}
.foot-body{left:25px;top:983px;width:847px;height:173px;background:#f2f2f2}
.foot-col{top:963px;font-family:"Abel",sans-serif;font-size:10.5px;color:#555}
.foot-col h4{font-size:13px;font-weight:normal;color:#222;margin-bottom:13px;letter-spacing:.5px}
.foot-col li{list-style:none;line-height:15.3px;letter-spacing:.4px}
.social li{display:flex;align-items:center;gap:8px;height:36.5px}
.social li i{width:22px;height:22px;border-radius:50%;background:#555;display:inline-block}
.cards{display:flex;gap:3px}
.cards span{width:29px;height:18px;border:1px solid #999;background:#fff;font-size:6px;color:#333;display:flex;align-items:center;justify-content:center}
.copyright{left:0;width:898px;top:1163px;text-align:center;font-family:"Abel",sans-serif;font-size:12px;color:#777;border-top:1px solid #ddd;padding-top:5px}
</style>
</head>
<body>
<header>
  <div class="abs brand"><div class="brand-name">DAPPER LADS<br>CLOTHING</div><div class="brand-tag">DESIGNER STYLE FOR MINIMEN</div></div>
  <div class="abs header-photo" role="img" aria-label="Photo of two smiling young boys lying together"></div>
  <div class="abs top-links"><span class="hl">Help</span> &nbsp;|&nbsp; Bookmark &nbsp;|&nbsp; My Account</div>
  <div class="abs account-bar">
    <span><i class="ico"></i>Login / Register</span>
    <span><i class="ico"></i>View Bag <span class="bag-count">00</span></span>
    <span class="total">Total: <b>AU($0.00)</b></span>
    <span><i class="ico"></i>Checkout</span>
  </div>
  <div class="abs search"><div class="field"></div><div class="btn">SEARCH</div></div>
  <div class="abs delivery-note">*Free Delivery on all Orders</div>
  <nav class="abs main-nav"><a>HOME</a><a>ABOUT US</a><a>BLOG</a><a>SIZING</a><a>MEDIA</a><a>CONTACT US</a></nav>
</header>

<aside>
  <div class="abs shop-title">SHOP</div>
  <ul class="abs shop-list">
    <li>T Shirts And Tops</li><li>Shirts And Jumpers</li><li>Pants And Shorts</li><li>Jeans</li><li>Jackets and Coats</li><li>Beachwear</li><li>Sleepwear</li><li>Shoes and Socks</li><li>Accessories</li><li>Bags &amp; Luggages</li><li>Gift Certificates</li>
  </ul>
  <div class="abs sale-box">
    <div class="abs sale-word">SALE</div>
    <div class="abs sale-panel"><span>Shop</span><span class="by">by Brand</span></div>
  </div>
</aside>

<main>
  <section class="abs frame hero">
    <div class="fill hero-img" role="img" aria-label="Photo of a young boy in a grey flat cap and plaid shirt"></div>
    <div class="abs hero-title">Designer Style<span>for MiniMen</span></div>
    <div class="abs save"><span class="v">SAVE</span><span class="big">50%</span><span class="upto">UP<br>TO</span><span class="on">on</span></div>
    <ul class="abs hero-items"><li>T Shirts</li><li>Jeans</li><li>Shorts</li><li>Jumpers</li></ul>
    <div class="abs shop-now" style="left:352px;top:334px;width:90px">SHOP NOW</div>
  </section>

  <div class="abs frame side-box" style="top:174px"><div class="fill" role="img" aria-label="Close-up photo of a boy in a grey cap" style="background:linear-gradient(180deg,#a9b8c2 0%,#9fadb6 30%,#d8b9a0 50%,#c59c83 75%,#5a5a5a 100%)"></div></div>
  <div class="abs frame side-box" style="top:303px"><div class="fill" role="img" aria-label="Photo of a green dinosaur backpack and lunch bag" style="background:linear-gradient(90deg,#c8c8c8 0%,#5f8a34 18%,#3c5d2c 45%,#7aa93c 65%,#35552b 85%,#c8c8c8 100%)"></div></div>
  <div class="abs frame side-box" style="top:432px"><div class="fill" style="background:#fff"><div class="abs gift-text"><span style="font-size:48px;line-height:48px;color:#999">Gift</span><span style="font-size:24px">CERTIFICATE</span></div></div></div>

  <div class="abs frame promo" style="left:25px;width:275px"><div class="fill" role="img" aria-label="Photo of a child's legs in jeans on steps beside a Latest arrow sign" style="background:linear-gradient(90deg,#5a5a5a 0%,#9a9a9a 25%,#3e4a5c 45%,#2c3646 60%,#b5b5b5 80%,#d8d8d8 100%)"><div class="shop-now">SHOP NOW</div></div></div>
  <div class="abs frame promo" style="left:312px;width:272px"><div class="fill" style="background:linear-gradient(90deg,#f4f4f4,#d6d6d6)">
    <div class="abs fs-title">Free shipping!</div>
    <div class="abs fs-sub">With purchases of</div>
    <div class="abs fs-price"><b>$150</b><small>OR MORE</small></div>
    <div class="shop-now">SHOP NOW</div>
  </div></div>
  <div class="abs frame promo" style="left:597px;width:275px"><div class="fill" style="background:#fff">
    <div class="abs nl-big">10%</div>
    <div class="abs nl-receive">Receive<b>OFF</b></div>
    <div class="abs nl-copy">you first order when<br>you sign up to our...</div>
    <div class="abs nl-word">NEWSLETTER</div>
    <div class="abs nl-email">email address...</div>
    <div class="abs nl-ok">OK</div>
  </div></div>

  <div class="abs feat-tab">FEATURED PRODUCTS</div>
  <section class="abs feat-box">
    <div class="abs arrow l"></div><div class="abs arrow r"></div>
    <div class="abs card" style="left:38px"><div class="pic" role="img" aria-label="Red t-shirt with patterned boxer shorts"><i style="background:linear-gradient(170deg,#e0282c 0%,#c81e22 50%,#3a2a40 75%,#f0e8f0 100%)"></i></div><div class="name">Rowe &amp; Harlan Boxer Set</div><div class="price">AU $22.50</div><div class="rrp">RRP: $44.95</div></div>
    <div class="abs card" style="left:197px"><div class="pic" role="img" aria-label="Dark denim kids shorts"><i style="background:linear-gradient(170deg,#3c4a5e,#26303f)"></i></div><div class="name">Marbury's Kids Shorts</div><div class="price">AU $30.00</div><div class="rrp">RRP: $59.95</div></div>
    <div class="abs card" style="left:356px"><div class="pic" role="img" aria-label="Green drawstring swim bag with dinosaur print"><i style="background:linear-gradient(170deg,#4f7a34,#2c4a2c 60%,#8fbb3c)"></i></div><div class="name">Library/Swim Bag Dinosaur</div><div class="price" style="top:164px">AU $24.95</div></div>
    <div class="abs card" style="left:515px"><div class="pic" role="img" aria-label="White kids t-shirt with printed cans graphic"><i style="background:linear-gradient(180deg,#f3f3f3 0%,#f3f3f3 30%,#777 45%,#555 60%,#f3f3f3 75%);border:1px solid #e4e4e4"></i></div><div class="name">Marbury's Kids T-Shirt Cans</div><div class="price">AU $19.95</div><div class="rrp">RRP: $39.95</div></div>
    <div class="abs card" style="left:674px"><div class="pic" role="img" aria-label="Green floral bucket hat"><i style="background:linear-gradient(170deg,#8ab35a,#5f8c3a 55%,#c6dcae)"></i></div><div class="name">Oakridge Bucket Hat</div><div class="price">AU $17.00</div><div class="rrp">RRP: $34.95</div></div>
  </section>
</main>

<footer>
  <div class="abs foot-head"></div>
  <div class="abs foot-body"></div>
  <div class="abs foot-col" style="left:66px"><h4>Customer Service</h4><ul><li>About Us</li><li>Contact Us</li><li>Blog</li><li>Press Releases</li><li>FAQ</li><li>Testimonials</li></ul></div>
  <div class="abs foot-col" style="left:234px"><h4>Shop With Us</h4><ul><li>Terms and Conditions</li><li>Privacy Policy</li><li>Payment Methods</li><li>StepWise Shoe Guides</li><li>Free Delivery &amp; Returns</li></ul></div>
  <div class="abs foot-col" style="left:416px"><h4>Shop Our Brands</h4><ul><li>Avenell</li><li>Bramble Art</li><li>Harrow Denim</li><li>Kenrow</li><li>Marbury's Kids</li><li>Plus4 Boys</li><li>Rowe &amp; Harlan</li><li>Oakridge</li><li>Chestnut Harbour</li><li>Zedmark</li></ul></div>
  <div class="abs foot-col" style="left:571px"><h4>Join us on</h4><ul class="social" style="margin-top:-6px"><li><i></i>Chatterbook</li><li><i></i>Linkwise</li><li><i></i>Tweetline</li><li><i></i>Contact Us</li></ul></div>
  <div class="abs foot-col" style="left:722px"><h4>Payment Methods</h4><div class="cards"><span>Merchcard</span><span>Versa</span><span>Amerigo</span><span>PayPort</span></div></div>
  <div class="abs copyright">© 2012-2013 Dapper Lads Clothing All right reserved.</div>
</footer>
</body>
</html>
```